Seeking funky, innovative business cards

I am looking to refresh our current business cards to something more engaging, visual and impactful. We are a management consultancy firm, see website (www.larkstone-partners.com.au). I've included our colour scheme, sample of the slides we use and our old business cards. We would like our cards to have icons. The card should display:- Name- Title- Mobile number- Address- Email address- Website - Company logo- Our purpose statement "We create the best places on earth to work"

Contact Information for Business Card

Brennan Ulfsson
Consultant
0468 927 341
Level 3, 218 Wexley Street, Melbourne 3000
brennan@larkstone-partners.com.au
www.larkstone-partners.com.au

Purpose statement "we create the best places on earth to work"
LOGO available in google images

Font styles to use
Other font styles liked:
• Open Sans Light, Bebas Neue (open to other cool foints)

Colors
ffc214
5c5c5c
f5f5f5
fefefe

Requirements
Must have
• - Name
• - Title
• - Mobile number
• - Address
• - Email address
• - Website
• - Company logo
• - Our purpose statement "We create the best places on earth to work"
Nice to have
• - Icons
• - Colour (see our colour scheme"

```html
<!DOCTYPE html>
<html lang="en">
<head>
<meta charset="utf-8">
<title>Larkstone Partners – Business Card</title>
<link rel="stylesheet" href="https://fonts.googleapis.com/css2?family=Open+Sans:wght@300;400;600;700&display=swap">
<style>
  :root {
    --brand-yellow: #ffc214;
    --brand-charcoal: #434546;
    --text-grey: #5c5c5c;
    --text-dark: #3a3a3a;
    --card-white: #fefefe;
    --page-bg: #e6e6e6;
  }
  * { box-sizing: border-box; margin: 0; padding: 0; }
  html, body {
    width: 1200px; height: 800px; overflow: hidden;
    background: var(--page-bg);
    font-family: "Open Sans", Arial, sans-serif;
  }
  .stage {
    width: 1200px; height: 800px;
    display: flex; align-items: center; justify-content: center; gap: 60px;
  }
  .card {
    width: 460px; height: 460px; position: relative; overflow: hidden;
    box-shadow: 0 10px 30px rgba(0,0,0,0.18);
  }

  /* Front */
  .card-front {
    background: var(--brand-charcoal);
    display: flex; align-items: center; justify-content: center;
  }
  .brand { display: flex; align-items: flex-start; gap: 14px; }
  .brand-dot {
    width: 14px; height: 14px; border-radius: 50%;
    background: var(--brand-yellow); margin-top: 30px;
  }
  .brand-name {
    display: flex; flex-direction: column;
    color: var(--card-white); font-weight: 300;
  }
  .brand-name-main { font-size: 66px; line-height: 1; letter-spacing: 0.5px; }
  .brand-name-sub {
    font-size: 13px; letter-spacing: 4px; text-transform: uppercase;
    margin-top: 10px; padding-left: 4px;
  }

  /* Back */
  .card-back { background: var(--card-white); }
  .contact {
    position: absolute; right: 56px; top: 92px; width: 350px; text-align: right;
    color: var(--text-grey); font-weight: 400; font-size: 17px; line-height: 1.5;
  }
  .contact-name { font-weight: 700; font-size: 26px; color: var(--text-dark); line-height: 1.2; }
  .contact-title { color: var(--brand-yellow); font-size: 18px; line-height: 1.4; }
  .divider {
    border: 0; border-top: 2px dotted var(--brand-yellow);
    width: 200px; margin: 16px 0 16px auto;
  }
  .web-domain { color: var(--brand-yellow); }
  .card-band { position: absolute; left: 0; right: 0; bottom: 0; height: 16px; display: flex; }
  .band-yellow { width: 48%; background: var(--brand-yellow); }
  .band-charcoal { flex: 1; background: var(--brand-charcoal); }
</style>
</head>
<body>
<main class="stage">
  <section class="card card-front" aria-label="Card front">
    <div class="brand">
      <span class="brand-dot"></span>
      <span class="brand-name">
        <span class="brand-name-main">Larkstone</span>
        <span class="brand-name-sub">Partners Australia</span>
      </span>
    </div>
  </section>

  <section class="card card-back" aria-label="Card back">
    <div class="contact">
      <p class="contact-name">Brennan Ulfsson</p>
      <p class="contact-title">Consultant</p>
      <hr class="divider">
      <p>Level 3, 218 Wexley Street</p>
      <p>Melbourne 3000</p>
      <hr class="divider">
      <p>0468 927 341</p>
      <p>brennan@larkstone-partners.com.au</p>
      <p>www.<span class="web-domain">larkstone-partners</span>.com.au</p>
    </div>
    <div class="card-band">
      <span class="band-yellow"></span>
      <span class="band-charcoal"></span>
    </div>
  </section>
</main>
</body>
</html>
```